Professional, modern and unique business card. We are looking to present a new look to our business cards however we don't want to divert too far away from original template. We want social media links and our 3 office addresses on the backside of the business cards. Please see attached business card templates for ideas.
Crestline Homes Color Code:
R: 7
G:63
B:86

Target Market(s)

Real Estate

Industry/Entity Type

Real Estate

Contact Information for Business Card

Follow the attached templates. In need of a more modern and unique touch but don't want to divert from the original theme or color.
Crestline Homes Color Code:
R: 7
G:63
B:86

Font styles to use
Serif

Requirements
Must have
• Crestline Homes logo, Crestline homes colors, social media links, 3 office addresses,
Nice to have
• information about Crestline Homes and QR codes. You can check out www.mycrestlinehomes.example

```html
<!DOCTYPE html>
<html lang="en">
<head>
<meta charset="utf-8">
<title>Crestline Homes – Business Card</title>
<link href="https://fonts.googleapis.com/css2?family=Lato:wght@400;700&display=swap" rel="stylesheet">
<style>
  :root {
    --page-bg: #2a2b2d;
    --card-navy: #073f56;
    --card-navy-deep: #06384d;
    --ink-light: #eef4f7;
    --ink-soft: #c9d9e1;
    --rule: rgba(238, 244, 247, 0.55);
  }
  * { margin: 0; padding: 0; box-sizing: border-box; }
  html, body { width: 1200px; height: 1108px; overflow: hidden; }
  body {
    background: var(--page-bg);
    font-family: "Lato", sans-serif;
    color: var(--ink-light);
    position: relative;
  }
  .card {
    position: absolute;
    top: 139px;
    width: 500px;
    height: 830px;
    border-radius: 30px;
    background: var(--card-navy);
    overflow: hidden;
  }
  .card--front { left: 80px; }
  .card--back { left: 620px; }

  /* Front */
  .brand {
    position: absolute;
    top: 230px;
    left: 0; right: 0;
    text-align: center;
  }
  .brand__name {
    font-weight: 700;
    font-size: 52px;
    letter-spacing: 2px;
    color: var(--ink-soft);
    text-transform: uppercase;
    line-height: 1;
  }
  .brand__sub {
    margin-top: 18px;
    font-weight: 700;
    font-size: 22px;
    letter-spacing: 20px;
    color: var(--ink-soft);
    text-transform: uppercase;
    padding-left: 20px;
  }
  .person {
    position: absolute;
    top: 520px;
    left: 0; right: 0;
    text-align: center;
  }
  .person__name {
    font-weight: 700;
    font-size: 25px;
    letter-spacing: 0.5px;
    text-transform: uppercase;
  }
  .person__title {
    font-size: 21px;
    margin-top: 2px;
  }
  .person__rule {
    width: 210px;
    height: 1px;
    background: var(--rule);
    margin: 14px auto 12px;
  }
  .contact { list-style: none; font-size: 20px; line-height: 1.42; }
  .contact b { font-weight: 700; }

  /* Back */
  .back__texture {
    position: absolute;
    inset: 0;
    background: linear-gradient(170deg, #0a4660 0%, var(--card-navy) 45%, var(--card-navy-deep) 100%);
  }
  .back__content {
    position: absolute;
    top: 268px;
    left: 0; right: 0;
    text-align: center;
  }
  .back__rule {
    width: 250px;
    height: 1px;
    background: var(--rule);
    margin: 0 auto;
  }
  .social-icons { display: block; margin: 14px auto 8px; }
  .social-list, .office-list { list-style: none; font-size: 21px; line-height: 1.3; }
  .social-list { margin-bottom: 16px; }
  .office-list { margin-top: 22px; }
</style>
</head>
<body>

<section class="card card--front" aria-label="Business card front">
  <div class="brand">
    <div class="brand__name">Crestline</div>
    <div class="brand__sub">Homes</div>
  </div>
  <div class="person">
    <div class="person__name">Daniel Mercer</div>
    <div class="person__title">Managing Director</div>
    <div class="person__rule"></div>
    <ul class="contact">
      <li><b>P:</b> 044-555 010 234</li>
      <li><b>M:</b> 044-555 010 234</li>
      <li><b>F:</b> 044-555 010 234</li>
      <li><b>E:</b> info@crestlinehomes.example</li>
      <li><b>W:</b>www.mycrestlinehomes.example</li>
    </ul>
  </div>
</section>

<section class="card card--back" aria-label="Business card back">
  <div class="back__texture" role="img" aria-label="Faint repeating brand-name pattern across the card background"></div>
  <div class="back__content">
    <div class="back__rule"></div>
    <svg class="social-icons" width="200" height="28" viewBox="0 0 200 28" aria-hidden="true">
      <g fill="var(--ink-light)">
        <circle cx="15" cy="14" r="12"/>
        <circle cx="49" cy="14" r="12"/>
        <circle cx="83" cy="14" r="12"/>
        <circle cx="117" cy="14" r="12"/>
        <circle cx="151" cy="14" r="12"/>
        <circle cx="185" cy="14" r="12"/>
      </g>
    </svg>
    <ul class="social-list">
      <li>CrestlinehomesNY</li>
      <li>Info at Crestline Homes</li>
      <li>@CrestlineHomesNY</li>
      <li>Crestline Homes</li>
      <li>Crestline Homes New York</li>
      <li>@CrestlineHomesQ</li>
    </ul>
    <div class="back__rule"></div>
    <ul class="office-list">
      <li class="office">418 Harbor View Rd<br>Maple Shore, NY 10990</li>
      <li class="office">72-30 Aspen Blvd<br>Birch Hollow, NY 10871</li>
      <li class="office">905 Orchard Ave<br>Fairmont, NY 10652</li>
    </ul>
  </div>
</section>

</body>
</html>
```